Redesign of business card for Cedar Ridge Mechanical

We are looking for a new design for our business cards for Cedar Ridge Mechanical. We are a plumbing & HVAC construction company, operating on the West Coast of Canada and USA. Logo attached.
Industry/Entity Type
Construction - Plumbing & HVAC
Contact Information for Business Card
Name, address, phone numbers, email, website address
Look and feel
Each slider illustrates characteristics of the customer's brand and the style your logo design should communicate.

```html
<!DOCTYPE html>
<html lang="en">
<head>
<meta charset="utf-8">
<title>Cedar Ridge Mechanical – Business Card</title>
<link href="https://fonts.googleapis.com/css2?family=Poppins:wght@400;500;700&display=swap" rel="stylesheet">
<style>
  :root {
    --stage: #b7b7b7;
    --ink: #0a0a0a;
    --paper: #ffffff;
    --rule: #8a8a8a;
    --dark-1: #000000;
    --dark-2: #1a1a1a;
  }
  * { margin: 0; padding: 0; box-sizing: border-box; }
  html, body { width: 1200px; height: 1200px; overflow: hidden; }
  body {
    background: var(--stage);
    font-family: "Poppins", sans-serif;
    position: relative;
  }
  .card {
    position: absolute;
    top: 303px;
    width: 368px;
    height: 594px;
  }
  .card-back {
    left: 201px;
    background: var(--dark-1);
    overflow: hidden;
  }
  .card-back .texture {
    position: absolute;
    inset: 0;
    background: radial-gradient(circle at 25% 25%, var(--dark-2) 0%, var(--dark-1) 55%),
                linear-gradient(160deg, transparent 60%, #151515 100%);
    background-blend-mode: screen;
  }
  .card-front {
    left: 599px;
    background: var(--paper);
    color: var(--ink);
    text-align: center;
  }
  .brand {
    position: absolute;
    display: flex;
    align-items: center;
    gap: 14px;
  }
  .brand-mark { width: 34px; height: 34px; flex: none; }
  .brand-name {
    font-weight: 700;
    font-size: 25px;
    line-height: 1.15;
    text-transform: uppercase;
    text-align: left;
    letter-spacing: 0.5px;
  }
  .card-back .brand { left: 44px; top: 380px; color: var(--paper); }
  .card-back .brand-mark { background: var(--paper); }
  .card-front .brand { left: 52px; top: 100px; color: var(--ink); }
  .card-front .brand-mark { background: var(--ink); }

  .person-name {
    position: absolute; top: 336px; left: 0; right: 0;
    font-weight: 700; font-size: 25px; letter-spacing: 0.3px;
  }
  .person-role {
    position: absolute; top: 368px; left: 0; right: 0;
    font-size: 16px;
  }
  .icon-row {
    position: absolute; top: 396px; left: 87px; width: 190px; height: 26px;
    display: flex; align-items: center; justify-content: center; gap: 4px;
  }
  .icon-row .rule { flex: 1; height: 1px; background: var(--rule); }
  .icon-row .rule:first-child { margin-right: 4px; }
  .icon-row .rule:last-child { margin-left: 4px; }
  .icon { width: 25px; height: 25px; background: var(--ink); border-radius: 4px; display: flex; align-items: center; justify-content: center; }
  .contact {
    position: absolute; top: 427px; left: 0; right: 0;
    font-size: 17px; line-height: 21px;
  }
  .divider { position: absolute; top: 507px; left: 88px; width: 194px; height: 1px; background: var(--rule); }
  .address {
    position: absolute; top: 519px; left: 0; right: 0;
    font-size: 17px; line-height: 21px;
  }
</style>
</head>
<body>
  <section class="card card-back">
    <div class="texture" role="img" aria-label="Dark geometric hexagon pattern background"></div>
    <div class="brand">
      <span class="brand-mark"></span>
      <span class="brand-name">Cedar Ridge<br>Mechanical</span>
    </div>
  </section>

  <section class="card card-front">
    <div class="brand">
      <span class="brand-mark"></span>
      <span class="brand-name">Cedar Ridge<br>Mechanical</span>
    </div>

    <h1 class="person-name">JONATHAN SMITH</h1>
    <p class="person-role">Managing Director</p>

    <div class="icon-row">
      <span class="rule"></span>
      <span class="icon">
        <svg width="15" height="15" viewBox="0 0 24 24" fill="#fff"><path d="M6.6 10.8a15 15 0 0 0 6.6 6.6l2.2-2.2c.3-.3.7-.4 1-.2 1.1.4 2.3.6 3.6.6.6 0 1 .4 1 1V20c0 .6-.4 1-1 1A17 17 0 0 1 3 4c0-.6.4-1 1-1h3.5c.6 0 1 .4 1 1 0 1.3.2 2.5.6 3.6.1.3 0 .7-.2 1z"/></svg>
      </span>
      <span class="icon">
        <svg width="15" height="15" viewBox="0 0 24 24" fill="none" stroke="#fff" stroke-width="2"><rect x="3" y="6" width="18" height="12"/><path d="M3 6l9 7 9-7"/></svg>
      </span>
      <span class="icon">
        <svg width="15" height="15" viewBox="0 0 24 24" fill="none" stroke="#fff" stroke-width="2"><circle cx="12" cy="12" r="9"/><path d="M3 12h18M12 3c3 3 3 15 0 18M12 3c-3 3-3 15 0 18"/></svg>
      </span>
      <span class="rule"></span>
    </div>

    <p class="contact">044-123 456 789<br>info@webname.com<br>www.websitename.com</p>
    <div class="divider"></div>
    <p class="address">421, Address line goes here<br>45452,Country Name</p>
  </section>
</body>
</html>
```